Business Card Design for Occupational Medicine Start Up Company

We need to design a professional business card. We are a healthcare company providing occupational medicine services to blue collar industries. We are professional, efficient and high quality service providers.

Target Market(s)

Blue Collar Industry: Shipbuilding, Ports, Trucking Companies; The Executives and Safety Officers for these companies

Industry/Entity Type

Healthcare

Contact Information for Business Card

Logo, Name, Title, Email, Phone

Other font styles liked:
• Please match our Brand Guide

Requirements
Must have
• Our Company Colors and Logo

```html
<!DOCTYPE html>
<html lang="en">
<head>
<meta charset="utf-8">
<title>CrewWell Clinics — Business Card</title>
<link rel="stylesheet" href="https://fonts.googleapis.com/css2?family=Montserrat:wght@500;600&display=swap">
<style>
  :root {
    --stage: #2a2a2a;
    --navy: #2f3079;
    --blue: #2f9ad6;
    --gold: #eeb04a;
    --paper: #f4f4f2;
    --white: #ffffff;
  }
  * { box-sizing: border-box; margin: 0; padding: 0; }
  html, body { width: 1200px; height: 1200px; overflow: hidden; }
  body {
    background: var(--stage);
    font-family: "Montserrat", Arial, sans-serif;
    position: relative;
  }
  .card {
    position: absolute;
    width: 594px;
    height: 348px;
    border-radius: 22px;
    overflow: hidden;
  }
  .card-front { left: 298px; top: 200px; background: var(--navy); }
  .card-back { left: 292px; top: 637px; background: var(--paper); }

  .brand-mark { position: absolute; border-radius: 50%; }
  .card-front .brand-mark {
    left: 258px; top: 24px; width: 300px; height: 300px;
    background: var(--blue);
  }
  .card-back .brand-mark {
    left: 33px; top: 48px; width: 92px; height: 92px;
    background: var(--blue);
  }

  .brand-name {
    position: absolute;
    font-weight: 600;
    letter-spacing: 0.5px;
    white-space: nowrap;
  }
  .card-front .brand-name { left: 30px; top: 262px; font-size: 21px; color: var(--white); }
  .card-back .brand-name { left: 148px; top: 76px; font-size: 30px; color: var(--navy); }

  .person { position: absolute; left: 31px; top: 188px; color: var(--navy); }
  .person-name { font-size: 25px; font-weight: 600; color: var(--blue); letter-spacing: 0.5px; }
  .person-title { font-size: 16px; font-weight: 500; margin-top: 2px; }
  .address { position: absolute; left: 31px; top: 257px; font-size: 16px; font-weight: 500; line-height: 22px; color: var(--navy); }

  .contacts { position: absolute; left: 338px; top: 189px; list-style: none; color: var(--navy); font-size: 16px; font-weight: 500; }
  .contacts li { display: flex; align-items: center; gap: 10px; height: 21.5px; }
  .contacts svg { width: 14px; height: 14px; flex: none; }

  .footer-stripes { position: absolute; left: 0; bottom: 0; width: 340px; height: 30px; }
  .footer-band {
    position: absolute; right: 0; bottom: 0; width: 320px; height: 44px;
    background: var(--navy);
    clip-path: polygon(8% 0, 100% 0, 100% 100%, 0 100%);
    color: var(--white); font-size: 15px; font-weight: 500;
    display: flex; align-items: center; padding-left: 58px;
  }
</style>
</head>
<body>
  <section class="card card-front" aria-label="Card front">
    <div class="brand-mark" role="img" aria-label="Brand symbol area"></div>
    <p class="brand-name">CREWWELL CLINICS</p>
  </section>

  <section class="card card-back" aria-label="Card back">
    <div class="brand-mark" role="img" aria-label="Brand symbol area"></div>
    <p class="brand-name">CREWWELL CLINICS</p>

    <div class="person">
      <p class="person-name">DANA MERCER</p>
      <p class="person-title">Senior Doctor</p>
    </div>
    <p class="address">48 Harbor Lane, Suite 210<br>Port Vale, State 54321</p>

    <ul class="contacts">
      <li>
        <svg viewBox="0 0 16 16" aria-hidden="true"><path fill="var(--blue)" d="M2 6c0-2 2-3 6-3s6 1 6 3l-2 1-1-2H5L4 7 2 6zm2 2h8l1 5H3l1-5zm4 1.5a1.5 1.5 0 100 3 1.5 1.5 0 000-3z"/></svg>
        555-010-2468
      </li>
      <li>
        <svg viewBox="0 0 16 16" aria-hidden="true"><rect x="1" y="3" width="14" height="10" fill="var(--navy)"/><path d="M1.5 3.5L8 9l6.5-5.5" stroke="var(--paper)" stroke-width="1.3" fill="none"/></svg>
        dana@crewwellclinics.com
      </li>
      <li>
        <svg viewBox="0 0 16 16" aria-hidden="true"><circle cx="8" cy="8" r="6.5" fill="var(--gold)"/><path d="M1.5 8h13M8 1.5v13M3 4.5h10M3 11.5h10" stroke="var(--paper)" stroke-width="0.9" fill="none"/><ellipse cx="8" cy="8" rx="3" ry="6.5" stroke="var(--paper)" stroke-width="0.9" fill="none"/></svg>
        www.crewwellclinics.com
      </li>
    </ul>

    <svg class="footer-stripes" viewBox="0 0 340 30" preserveAspectRatio="none" aria-hidden="true">
      <rect x="0" y="4" width="340" height="4" fill="var(--blue)"/>
      <rect x="0" y="13" width="340" height="4" fill="var(--navy)"/>
      <rect x="0" y="23" width="340" height="7" fill="var(--gold)"/>
    </svg>
    <div class="footer-band">Occupational Medicine</div>
  </section>
</body>
</html>
```